Website Design - TallyPorchHelpers.net

PLEASE CHECK WORD DOCUMENT ATTACHED FOR WEBSITE FLOW.

Target Market(s)

REAL ESTATE AGENTS ARE THE TARGET MARKET

Industry/Entity Type

Real Estate

Coding

Coded - Design and coding required

Number of Pages Required

4 page

Colors

Designer to choose colors to be used in the design.

Requirements
Must have
• WE LIKE RED LOGO ATTACHED
Nice to have
• PLEASE CHECK WORD DOCUMENT ATTACHED FOR WEBSITE FLOW.
Should not have

```html
<!DOCTYPE html>
<html lang="en">
<head>
<meta charset="utf-8">
<title>About Us – TallyPorchHelpers.net</title>
<link rel="stylesheet" href="https://fonts.googleapis.com/css2?family=Roboto:wght@400;500&family=Roboto+Condensed:wght@400&family=Open+Sans:wght@400;600&display=swap">
<style>
:root{
  --brand-red:#e3101f;
  --navy:#0b1f4a;
  --navy-deep:#131a25;
  --hero-blue:#2b4a80;
  --ink:#222;
  --body-text:#555;
  --team-bg:#dde8f6;
  --card-bg:#f4f4f4;
  --accent-blue:#1f5fc0;
  --white:#fff;
}
*{margin:0;padding:0;box-sizing:border-box}
html,body{width:1200px;height:2261px;overflow:hidden;background:var(--white)}
body{position:relative;font-family:"Roboto",Arial,sans-serif;color:var(--ink)}
.abs{position:absolute}

/* header */
.site-header{position:absolute;left:0;top:0;width:1200px;height:124px;background:var(--white)}
.brand{left:89px;top:44px;display:flex;align-items:center;gap:10px;font-size:22px;font-weight:500;color:var(--brand-red)}
.brand-dot{width:16px;height:16px;background:var(--brand-red)}
.call-line{left:856px;top:27px;display:flex;align-items:center;gap:10px;font-size:16px;color:var(--ink)}
.main-nav{right:87px;top:70px;display:flex;gap:51px;font-size:16px;color:var(--ink)}

/* hero */
.page-hero{left:0;top:124px;width:1200px;height:169px;background:linear-gradient(90deg,#1c3566,var(--hero-blue) 50%,#1c3566)}
.page-hero h1{position:absolute;width:100%;top:62px;text-align:center;font:400 35px "Roboto Condensed",Arial,sans-serif;color:var(--white)}

/* about */
.about-frame{left:92px;top:383px;width:354px;height:323px;border:2px solid #555}
.about-photo{left:118px;top:404px;width:378px;height:332px;background:linear-gradient(160deg,#7d6a5a,#6f8d9a 40%,#6aa642 75%,#8ec63f);box-shadow:0 6px 22px rgba(0,0,0,.35)}
.about-title{left:526px;top:418px;font-size:30px;font-weight:400;color:var(--ink)}
.about-lead{left:529px;top:470px;width:561px;font-size:16px;line-height:28.6px;color:var(--body-text);text-align:justify}
.about-body{left:101px;top:770px;width:1003px;font-size:16px;line-height:29.7px;color:var(--body-text);text-align:justify}

/* team */
.team{left:0;top:1063px;width:1200px;height:781px;background:var(--team-bg)}
.team h2{position:absolute;width:100%;top:82px;text-align:center;font:400 34px "Roboto Condensed",Arial,sans-serif;color:var(--ink)}
.team-card{position:absolute;top:243px;width:312px;height:410px;background:var(--card-bg);box-shadow:0 2px 8px rgba(0,0,0,.2);text-align:center;font-family:"Open Sans",Arial,sans-serif}
.team-avatar{position:absolute;left:89px;top:-60px;width:133px;height:133px;border-radius:50%;background:linear-gradient(180deg,#b9bcc2,#3c4656)}
.team-name{margin-top:93px;font:400 17px "Roboto",Arial,sans-serif;color:var(--ink)}
.team-role{margin-top:4px;font:400 15px "Roboto",Arial,sans-serif;color:var(--accent-blue)}
.team-bio{margin:14px auto 0;width:262px;font-size:14.5px;line-height:25.5px;color:#555}
.team-bio+.team-bio{margin-top:13px}
.team-social{display:flex;justify-content:center;gap:14px;margin-top:28px}
.social-dot{width:28px;height:28px;border-radius:50%;border:1.5px solid #2a4a9a}
.social-dot.alt{border-color:#1da1f2}
.social-dot.red{border-color:#d9443a}
.slider-arrow{position:absolute;top:1427px;width:58px;height:58px;border-radius:50%;background:var(--white);box-shadow:0 1px 6px rgba(0,0,0,.15)}

/* footer */
.site-footer{left:0;top:1844px;width:1200px;height:346px;background:var(--navy);color:var(--white);font-family:"Open Sans",Arial,sans-serif}
.footer-title{position:absolute;top:83px;font-size:21px;font-weight:400;letter-spacing:.5px}
.footer-about{position:absolute;left:87px;top:128px;width:330px;font-size:15.5px;line-height:24.5px}
.contact-item{position:absolute;left:513px;display:flex;gap:13px}
.contact-item h4{font-size:16.5px;font-weight:600}
.contact-item p{font-size:14px;line-height:21px}
.field{position:absolute;border:1px solid #cfd6e4;background:var(--white);font-size:14px;color:#333;padding:8px 4px}
.submit{position:absolute;left:813px;top:262px;width:104px;height:31px;background:var(--accent-blue);color:var(--white);font-size:16px;text-align:center;line-height:31px}
.legal{left:0;top:2190px;width:1200px;height:71px;background:var(--navy-deep);color:#aab;font:14px "Open Sans",Arial,sans-serif;text-align:center;line-height:71px}
</style>
</head>
<body>

<header class="site-header">
  <div class="abs brand"><span class="brand-dot"></span>TallyPorchHelpers.net</div>
  <div class="abs call-line">
    <svg width="26" height="26" viewBox="0 0 26 26" aria-hidden="true"><circle cx="13" cy="13" r="11.5" fill="none" stroke="#1f5fc0" stroke-width="2"/><path d="M8.5 7.5l2.5-.5 1.3 3-1.6 1.2a8 8 0 003.8 3.8l1.2-1.6 3 1.3-.5 2.5c-5.5.5-10.2-4.2-9.7-9.7z" fill="#1f5fc0"/></svg>
    Call Or Text Us 1-555-014-2287
  </div>
  <nav class="abs main-nav"><span>How it works</span><span>Service</span><span>Pricing</span><span>About us</span><span>Faq</span><span>Contact</span></nav>
</header>

<section class="abs page-hero" role="img" aria-label="Dimmed photo of a suburban house under a blue overlay"><h1>ABOUT US</h1></section>

<div class="abs about-frame"></div>
<div class="abs about-photo" role="img" aria-label="Photo of a for-sale yard sign in front of a house with a flowering garden"></div>
<h2 class="abs about-title">Neque porro quisquam est qui dolorem</h2>
<p class="abs about-lead">It is a long established fact that a reader will be distracted by the readable content of a page when looking at its layout. The point of using Lorem Ipsum is that it has a more-or-less normal distribution of letters, as opposed to using 'Content here, content here', making it look like readable English. Many desktop publishing packages and web page editors now use Lorem Ipsum as their default model text, and a search for 'lorem ipsum' will uncover many web sites still in their infancy The point of using Lorem Ipsum is that it has a more-or-less normal distribution of letters, as opposed to using 'Content here, content here', making it look like readable English. Many desktop publishing packages</p>
<p class="abs about-body">It is a long established fact that a reader will be distracted by the readable content of a page when looking at its layout. The point of using Lorem Ipsum is that it has a more-or-less normal distribution of letters, as opposed to using 'Content here, content here', making it look like readable English. Many desktop publishing packages and web page editors now use Lorem Ipsum as their default model text, and a search for 'lorem ipsum' will uncover many web sites still in their infancy The point of using Lorem Ipsum is that it has a more-or-less normal distribution of letters, as opposed to using 'Content here, content here', making it look like readable English. Many desktop publishing packages and web page editors now use Lorem Ipsum as their default model text, and a search for 'lorem ipsum' will uncover many web sites still in their infancy.</p>

<section class="abs team">
  <h2>MEET THE TEAM</h2>
  <article class="team-card" style="left:101px">
    <div class="team-avatar" role="img" aria-label="Portrait photo of the managing partner"></div>
    <h3 class="team-name">Neque porro quisquam</h3>
    <p class="team-role">Managing Partner</p>
    <p class="team-bio">Lorem Ipsum is simply dummy text of the printing and typesetting industry. Lorem Ipsum has been the industry</p>
    <p class="team-bio">Standard dummy text ever since the 1500s, when an unknown printer took a galley of type and scrambled.</p>
    <div class="team-social"><span class="social-dot"></span><span class="social-dot alt"></span><span class="social-dot red"></span></div>
  </article>
  <article class="team-card" style="left:440px">
    <div class="team-avatar" role="img" aria-label="Portrait photo of a senior partner"></div>
    <h3 class="team-name">Dolorem ipsum quia</h3>
    <p class="team-role">Senior Partner</p>
    <p class="team-bio">Lorem Ipsum is simply dummy text of the printing and typesetting industry. Lorem Ipsum has been the industry</p>
    <p class="team-bio">Standard dummy text ever since the 1500s, when an unknown printer took a galley of type and scrambled.</p>
    <div class="team-social"><span class="social-dot"></span><span class="social-dot alt"></span><span class="social-dot red"></span></div>
  </article>
  <article class="team-card" style="left:779px">
    <div class="team-avatar" role="img" aria-label="Portrait photo of a senior partner"></div>
    <h3 class="team-name">Porro quisquam est</h3>
    <p class="team-role">Senior Partner</p>
    <p class="team-bio">Lorem Ipsum is simply dummy text of the printing and typesetting industry. Lorem Ipsum has been the industry</p>
    <p class="team-bio">Standard dummy text ever since the 1500s, when an unknown printer took a galley of type and scrambled.</p>
    <div class="team-social"><span class="social-dot"></span><span class="social-dot alt"></span><span class="social-dot red"></span></div>
  </article>
</section>
<div class="slider-arrow" style="left:36px"><svg width="58" height="58" viewBox="0 0 58 58" aria-hidden="true"><path d="M33 18L22 29l11 11" fill="none" stroke="#333" stroke-width="2"/></svg></div>
<div class="slider-arrow" style="left:1125px"><svg width="58" height="58" viewBox="0 0 58 58" aria-hidden="true"><path d="M25 18l11 11-11 11" fill="none" stroke="#333" stroke-width="2"/></svg></div>

<footer class="abs site-footer">
  <h3 class="footer-title" style="left:87px">ABOUT US</h3>
  <p class="footer-about">Owned and operated by a Highly Experienced and Skilled Promoter, An Expert Marketer and a Savvy Realtor, we help agents leverage their time and skills to increase production at an affordable price with impeccable support!</p>

  <h3 class="footer-title" style="left:517px">CONTACT US</h3>
  <div class="contact-item" style="top:130px">
    <svg width="20" height="26" viewBox="0 0 20 26" aria-hidden="true"><path d="M10 1.5a8 8 0 00-8 8c0 6 8 15 8 15s8-9 8-15a8 8 0 00-8-8z" fill="none" stroke="#fff" stroke-width="1.5"/><circle cx="10" cy="9.5" r="3" fill="none" stroke="#fff" stroke-width="1.5"/></svg>
    <div><h4>ADDRESS</h4><p>48 Lantern Row, Suite B<br>Fairhollow, NC 27000</p></div>
  </div>
  <div class="contact-item" style="top:212px">
    <svg width="20" height="22" viewBox="0 0 20 22" aria-hidden="true"><path d="M3 2l4-.5 2 4.5-2.3 1.7a11 11 0 006 6L14.5 11.5l4.5 2-.5 4C10 18.5 2 10.5 3 2z" fill="none" stroke="#fff" stroke-width="1.5"/></svg>
    <div><h4>PHONE NUMBER</h4><p>1-555-014-2287</p></div>
  </div>

  <h3 class="footer-title" style="left:813px">CONTACT FORM</h3>
  <div class="field" style="left:813px;top:130px;width:148px;height:36px">Name</div>
  <div class="field" style="left:965px;top:130px;width:148px;height:36px">Cell Phone</div>
  <div class="field" style="left:813px;top:172px;width:300px;height:36px">Email</div>
  <div class="field" style="left:813px;top:215px;width:300px;height:37px">Message</div>
  <div class="submit">Submit</div>
</footer>

<div class="abs legal">© 2018 Company Name&nbsp; All right reserved</div>

</body>
</html>
```